Hardcore nerd needs to stand out in a sea of dull Defence business cards

Wombarra Devices is a new Australian consulting engineering company that turns research and theory into practical systems. No evangelistic fluff, just mathematics and physics into electronic and optical circuits for consumer products, scientific research or Defence applications.

We already have a recognised logo (provided) which is often dark blue/black on a light background but we're open to other combinations. (Us engineers tend to have limited aesthetic imagination :)

Some of our recent products have included:
* Instrumentation for electrical testing,
* Radar jammers,
* GPS antenna design,
* Satellite tracking systems,
* High power lasers

We're open to both single and double-sided designs - happy to be convinced either way.

P.S. Another group is working on the web page, so - alas - our web site is currently of no use for images/ideas...

Target Market(s)

Engineering managers,
Scientists

Contact Information for Business Card

Dr Colin Harte
R&D Engineer

colin@wombarradevices.com.au
0427 563 710

PO Box XXX (to be confirmed)
Kelsby ACT 2917
Australia

Font styles to use
Serif
Sans Serif

Colors

Designer to choose colors to be used in the design.

Requirements
Must have
• My contact details!
• I've had many (great) "bold and plain" designs submitted already, so feel free to be artistically creative :)
• Happy to take advice re fonts/colours/printability etc.
Nice to have
• I'm not sure if "lists" are more at home on a CV than a business card, but representative services include:
• Applied electromagnetics
• RF and high speed electronics
• Signal and image processing
• Electro-optical and laser systems
• Concept-to-prototype design services
• If you're considering double sided cards, then often measuring/alignment grids/rulers feature on the back of similar cards.
• e.g. https://www.veltranoptics.example/newgrouppage9.cfm?objectgroup_id=4183
• https://www.veltranoptics.example/newgrouppage9.cfm?objectgroup_ID=4185
• ..or even a "Smith chart" (google will return lots)
• Generic images to represent a capability might work - googling images associated with keyword for each of these areas might help:
• - "passive radar", "phased array", "fdtd", "vircator"
• RF and high speed electronic design
• - "smith chart", "microstrip circuits", "dimensioned drawing", "electronic schematic"
• - "dft", "iir filter"
• - "optical cavity". "laser energy level diagram"
• Background/watermarked images outlines/wireframes/schematics would probably look OK.
Should not have
• If a list of projects/services is provided, it is important not to make the client feel that this is "all" the company can do. Engineering design is a creative discipline (like graphics :)
• Please, no stock "military" snaps like planes, missiles, etc!

```html
<!DOCTYPE html>
<html lang="en">
<head>
<meta charset="utf-8">
<title>Wombarra Devices – Business Card</title>
<link rel="stylesheet" href="https://fonts.googleapis.com/css2?family=Lato:wght@400;700;900&display=swap">
<style>
  :root {
    --stage: #353535;
    --card-dark: #3a3a3a;
    --card-light: #ffffff;
    --ink: #333333;
    --ink-soft: #6b6b6b;
    --rule: #555555;
    --on-dark: #ffffff;
  }
  * { box-sizing: border-box; margin: 0; padding: 0; }
  html, body {
    width: 1200px; height: 675px; overflow: hidden;
    background: var(--stage);
    font-family: "Lato", sans-serif;
  }
  .stage {
    width: 1200px; height: 675px;
    display: flex; align-items: center; justify-content: center; gap: 36px;
  }
  .card {
    width: 540px; height: 310px; position: relative;
    box-shadow: 0 10px 24px rgba(0,0,0,.45);
  }

  /* Back */
  .card--back { background: var(--card-dark); color: var(--on-dark); }
  .card--back .brand {
    position: absolute; left: 42px; top: 112px;
    display: flex; align-items: center; gap: 12px;
  }
  .brand-dot { width: 34px; height: 34px; border-radius: 50%; flex: none; }
  .card--back .brand-dot { background: var(--on-dark); }
  .brand-name { font-weight: 900; font-size: 22px; line-height: 1.05; text-transform: uppercase; letter-spacing: .5px; }
  .card--back .brand-name { color: var(--on-dark); }
  .services { position: absolute; left: 262px; top: 76px; }
  .services-title { font-size: 17px; font-weight: 400; margin-bottom: 8px; }
  .services-list { list-style: none; font-size: 12.5px; line-height: 1.65; }
  .services-list li { display: flex; align-items: center; gap: 7px; }
  .tick { width: 10px; height: 10px; flex: none; }

  /* Front */
  .card--front { background: var(--card-light); color: var(--ink); }
  .card--front .brand {
    position: absolute; left: 34px; top: 130px;
    display: flex; align-items: center; gap: 10px;
  }
  .card--front .brand-dot { background: var(--ink); }
  .card--front .brand-name { color: var(--ink); font-size: 20px; }
  .divider { position: absolute; left: 262px; top: 70px; width: 1px; height: 170px; background: var(--rule); }
  .contact { position: absolute; left: 284px; top: 72px; }
  .person-name { font-size: 17px; font-weight: 700; color: var(--ink); }
  .person-role { font-size: 11px; color: var(--ink-soft); margin-bottom: 12px; }
  .address { font-size: 11px; line-height: 1.45; color: var(--ink-soft); margin-bottom: 10px; }
  .lines { list-style: none; font-size: 11px; line-height: 1.6; color: var(--ink-soft); }
  .lines li { display: flex; align-items: center; gap: 6px; }
  .icon { width: 10px; height: 10px; flex: none; fill: var(--ink); }
</style>
</head>
<body>
<main class="stage">

  <section class="card card--back" aria-label="Card back">
    <div class="brand">
      <span class="brand-dot"></span>
      <span class="brand-name">Wombarra<br>Devices</span>
    </div>
    <div class="services">
      <h2 class="services-title">Our Services:</h2>
      <ul class="services-list">
        <li><svg class="tick" viewBox="0 0 10 10"><path d="M1 5.5 L4 8.5 L9 1.5" fill="none" stroke="#fff" stroke-width="2"/></svg>Applied electromagnetics</li>
        <li><svg class="tick" viewBox="0 0 10 10"><path d="M1 5.5 L4 8.5 L9 1.5" fill="none" stroke="#fff" stroke-width="2"/></svg>RF and high speed electronics</li>
        <li><svg class="tick" viewBox="0 0 10 10"><path d="M1 5.5 L4 8.5 L9 1.5" fill="none" stroke="#fff" stroke-width="2"/></svg>Signal and image processing</li>
        <li><svg class="tick" viewBox="0 0 10 10"><path d="M1 5.5 L4 8.5 L9 1.5" fill="none" stroke="#fff" stroke-width="2"/></svg>Electro-optical and laser systems</li>
        <li><svg class="tick" viewBox="0 0 10 10"><path d="M1 5.5 L4 8.5 L9 1.5" fill="none" stroke="#fff" stroke-width="2"/></svg>Concept-to-prototype design services</li>
      </ul>
    </div>
  </section>

  <section class="card card--front" aria-label="Card front">
    <div class="brand">
      <span class="brand-dot"></span>
      <span class="brand-name">Wombarra<br>Devices</span>
    </div>
    <div class="divider"></div>
    <div class="contact">
      <h1 class="person-name">Dr Colin Harte</h1>
      <p class="person-role">R&amp;D Engineer</p>
      <p class="address">PO Box XXX (to be confirmed)<br>Kelsby ACT 2917, Australia</p>
      <ul class="lines">
        <li><svg class="icon" viewBox="0 0 10 10"><path d="M2 0.5 L3.8 2.6 L2.8 3.8 Q4 6 6.2 7.2 L7.4 6.2 L9.5 8 L8.2 9.5 Q4.5 9.3 2 6.8 Q0 4.5 0.5 1.8 Z"/></svg>0427 563 710</li>
        <li><svg class="icon" viewBox="0 0 10 10"><path d="M0.5 2 H9.5 V8 H0.5 Z M1 2.4 L5 5.6 L9 2.4" fill="none" stroke="#333" stroke-width="1"/></svg>colin@wombarradevices.com.au</li>
        <li><svg class="icon" viewBox="0 0 10 10"><g fill="none" stroke="#333" stroke-width=".9"><circle cx="5" cy="5" r="4.3"/><ellipse cx="5" cy="5" rx="1.9" ry="4.3"/><path d="M0.7 5 H9.3"/></g></svg>wombarradevices.com.au</li>
      </ul>
    </div>
  </section>

</main>
</body>
</html>
```